Business Card Design

We need a business card designed for our new company. Prefer a black card with white logo & writing.

Contact Information for Business Card

Ted Galloway, address: 7-4812 Fernhollow Road, Abbotsford, BC, V3K 8R2, Office Phone: 604-712-3390, Cell: 604-947-2164, Email: ted@resinworkshub.ca

Colors

Designer to choose only greyscale colors for use in the design.

```html
<!DOCTYPE html>
<html lang="en">
<head>
<meta charset="utf-8">
<title>Resin Works Hub — Business Card</title>
<link rel="stylesheet" href="https://fonts.googleapis.com/css2?family=Montserrat:wght@400;600;700;800&display=swap">
<style>
  :root {
    --stage: #d9d9d9;
    --card: #252525;
    --card-back: #1c1c1c;
    --ink: #ffffff;
    --ink-soft: #d6d6d6;
    --ink-muted: #bdbdbd;
    --pattern-light: #4a4a4a;
    --pattern-dark: #141414;
  }
  * { margin: 0; padding: 0; box-sizing: border-box; }
  html, body {
    width: 900px; height: 1200px; overflow: hidden;
    background: var(--stage);
    font-family: "Montserrat", Arial, sans-serif;
  }
  .canvas { position: relative; width: 900px; height: 1200px; }

  .card {
    position: absolute; left: 80px; width: 742px; height: 441px;
    border-radius: 22px; overflow: hidden;
    box-shadow: 0 8px 18px rgba(0,0,0,0.35);
  }
  .card--front { top: 131px; background: var(--card); }
  .card--back { top: 638px; background: var(--card-back); }

  .brand-name {
    position: absolute; left: 0; right: 0; top: 96px;
    text-align: center; color: var(--ink);
    font-weight: 800; font-size: 44px; letter-spacing: 1px;
  }

  .person { position: absolute; right: 398px; top: 277px; text-align: right; }
  .person__name { color: var(--ink); font-weight: 700; font-size: 25px; line-height: 1.2; }
  .person__role { color: var(--ink-muted); font-weight: 400; font-size: 15px; margin-top: 8px; }

  .divider {
    position: absolute; left: 371px; top: 257px; width: 2px; height: 100px;
    background: var(--ink);
  }

  .contact-list { position: absolute; left: 394px; top: 254px; list-style: none; }
  .contact-list li {
    display: flex; align-items: center; height: 27px;
    color: var(--ink-soft); font-size: 15px; font-weight: 400;
  }
  .contact-list li:nth-child(2) { margin-bottom: 1px; }
  .contact-list svg { width: 15px; height: 15px; margin-right: 12px; fill: var(--ink); flex: none; }

  .address {
    position: absolute; left: 0; right: 0; top: 389px;
    text-align: center; color: var(--ink-soft); font-size: 15.5px; font-weight: 400;
  }

  .pattern-fill {
    position: absolute; inset: 0;
    background: linear-gradient(100deg, var(--pattern-light) 0%, #2c2c2c 35%, var(--pattern-dark) 60%, var(--card-back) 100%);
    opacity: 0.85;
  }
  .back-brand {
    position: absolute; left: 498px; top: 318px; width: 116px;
    text-align: center; color: var(--ink);
    font-weight: 800; font-size: 15px; line-height: 1.15;
  }
</style>
</head>
<body>
<main class="canvas">

  <section class="card card--front" aria-label="Business card front">
    <div class="brand-name">RESIN WORKS HUB</div>

    <div class="person">
      <div class="person__name">Ted Galloway</div>
      <div class="person__role">owner</div>
    </div>

    <div class="divider"></div>

    <ul class="contact-list">
      <li>
        <svg viewBox="0 0 24 24" aria-hidden="true"><path d="M6.6 10.8a15.1 15.1 0 0 0 6.6 6.6l2.2-2.2a1 1 0 0 1 1-.25 11.4 11.4 0 0 0 3.6.57 1 1 0 0 1 1 1V20a1 1 0 0 1-1 1A17 17 0 0 1 3 4a1 1 0 0 1 1-1h3.5a1 1 0 0 1 1 1c0 1.25.2 2.45.57 3.6a1 1 0 0 1-.25 1z"/></svg>
        604-712-3390
      </li>
      <li>
        <svg viewBox="0 0 24 24" aria-hidden="true"><path d="M8 1h8a2 2 0 0 1 2 2v18a2 2 0 0 1-2 2H8a2 2 0 0 1-2-2V3a2 2 0 0 1 2-2zm0 3v14h8V4zm4 15.5a1 1 0 1 0 0 2 1 1 0 0 0 0-2z"/></svg>
        604-947-2164
      </li>
      <li>
        <svg viewBox="0 0 24 24" aria-hidden="true"><path d="M2 5h20v14H2zm2 2v.4l8 5 8-5V7l-8 5z"/></svg>
        ted@resinworkshub.ca
      </li>
      <li>
        <svg viewBox="0 0 24 24" aria-hidden="true"><path d="M12 2a10 10 0 1 0 0 20 10 10 0 0 0 0-20zm6.9 6h-3a15.7 15.7 0 0 0-1.4-3.6A8 8 0 0 1 18.9 8zM12 4c.8 1.2 1.5 2.5 1.9 4h-3.8c.4-1.5 1.1-2.8 1.9-4zM4.3 14a8.2 8.2 0 0 1 0-4h3.4a16.5 16.5 0 0 0 0 4zm.8 2h3a15.7 15.7 0 0 0 1.4 3.6A8 8 0 0 1 5.1 16zm3-8h-3a8 8 0 0 1 4.4-3.6A15.7 15.7 0 0 0 8.1 8zM12 20c-.8-1.2-1.5-2.5-1.9-4h3.8c-.4 1.5-1.1 2.8-1.9 4zm2.3-6H9.7a14.7 14.7 0 0 1 0-4h4.6a14.7 14.7 0 0 1 0 4zm.2 5.6a15.7 15.7 0 0 0 1.4-3.6h3a8 8 0 0 1-4.4 3.6zm1.8-5.6a16.5 16.5 0 0 0 0-4h3.4a8.2 8.2 0 0 1 0 4z"/></svg>
        www.resinworkshub.ca
      </li>
    </ul>

    <div class="address">7-4812 Fernhollow Road, Abbotsford, BC, V3K 8R2</div>
  </section>

  <section class="card card--back" aria-label="Business card back">
    <div class="pattern-fill" role="img" aria-label="Faint repeating brand pattern in glossy dark grey, fading from lighter grey at left to black at right"></div>
    <div class="back-brand">RESIN WORKS HUB</div>
  </section>

</main>
</body>
</html>
```